I need a complete stationary pack for a real estate office that sells and manages residential proper

We need a stationary design pack for my real estate office called ‘brightkeyhomes’ that is in Queensland Australia. My offices are both in suburban and coastal locations in the south west corner of Queensland at the Coral Bay Shore and Brisbane.
We predominately manage real estate on behalf of owners and sell property in the residential sector.
I have attached a copy of our existing design of my business card and do like the current concept/layout. In saying this you may be able to use this existing theme across to the other items required or see opportunity on how to improve what I have already.
I would like to see concepts for the following products:
- Letterhead
- Fax header
- Business cards
- Email signature
- With complements slips and
- Envelopes
I have attached our current logo that was designed by Artfolder and the font is Prelo.

I am looking for a contemporary design that is professional and reflects trust and professionalism. I am currently using the logo with a black background on some material as per the following link

http://www.plotlisting.com.au/property/for-sale/house/qld/merridale/?adid=4827305118&sp=7

I have posted another job 517362 for signage and the company car signage done too if you are interested.

Please do not hesitate to contact me should you have any questions. Thank you.

Target Market(s)

Western speaking people aged from 25 to 60 from modest backgrounds to well off individuals

Industry/Entity Type

Real Estate

Requirements
Must have
• Professional in appearance, show a mature and trustworthy image
Should not have
• As there is good colour with the logo, i am do not want over the top designs or colours

```html
<!DOCTYPE html>
<html lang="en">
<head>
<meta charset="utf-8">
<title>brightkeyhomes stationery pack</title>
<link rel="stylesheet" href="https://fonts.googleapis.com/css2?family=Source+Sans+3:ital,wght@0,400;0,600;0,700;1,400&display=swap">
<style>
:root{
  --board:#1c1c1c;
  --paper:#ffffff;
  --ink:#2f3a4a;
  --muted:#555c66;
  --rule:#8a8f96;
  --orange:#f7941d;
  --purple:#6b2c7a;
  --blue:#1b75bc;
  --red:#d7282f;
  --green:#2e9e48;
  --photo:#7d8ea3;
  --window:#e4e5e7;
}
*{box-sizing:border-box;margin:0;padding:0}
html,body{width:1200px;height:900px;overflow:hidden}
body{background:var(--board);font-family:"Source Sans 3",Arial,sans-serif;color:var(--muted);position:relative}
.piece{position:absolute;background:var(--paper);overflow:hidden;box-shadow:0 2px 6px rgba(0,0,0,.5)}
.band{position:absolute;inset:0;width:100%;height:100%}
.fill-orange{fill:var(--orange)}
.fill-purple{fill:var(--purple)}
.fill-blue{fill:var(--blue)}
.fill-paper{fill:var(--paper)}
.wordmark{position:absolute;display:flex;align-items:center;gap:.35em;color:var(--ink);font-weight:600;letter-spacing:-.01em;white-space:nowrap}
.wordmark::before{content:"";width:1.6em;height:1.6em;border-radius:50%;background:var(--orange);flex:none}
.contact{position:absolute;font-size:6px;line-height:1.35;color:var(--muted)}
.contact svg{width:6px;height:6px;vertical-align:-1px;margin-right:2px}
.icon{fill:var(--red)}
.photo{position:absolute;background:linear-gradient(180deg,#b8c4d2,var(--photo) 60%,#3a4656)}
.person-name{color:var(--blue);font-weight:700}
.person-role{color:var(--green)}

/* letterhead */
.letterhead{left:18px;top:30px;width:298px;height:422px}
.letterhead .wordmark{left:38px;top:66px;font-size:15px}
.letterhead .contact{left:194px;top:46px}

/* fax header */
.fax{left:331px;top:30px;width:298px;height:422px}
.fax .wordmark{left:22px;top:42px;font-size:12px}
.fax .contact{left:194px;top:40px}
.fax-title{position:absolute;right:18px;top:96px;font-size:10px;font-weight:700;color:var(--ink)}
.fax-table{position:absolute;left:20px;top:112px;width:262px;border-collapse:collapse;font-size:6px;color:var(--ink)}
.fax-table td{border:.6px solid var(--ink);height:12.4px;padding:0 5px}
.fax-table .label{width:48px}
.fax-options{position:absolute;left:20px;top:170px;display:flex;gap:10px;font-size:6px;color:var(--ink)}
.fax-options span::before{content:"";display:inline-block;width:6px;height:6px;border:.6px solid var(--ink);margin-right:3px;vertical-align:-1px}

/* folder cover */
.cover{left:646px;top:20px;width:313px;height:440px}
.cover .wordmark{left:82px;top:258px;font-size:22px}

/* business cards */
.card{left:975px;width:205px}
.card-front-a{top:20px;height:116px}
.card-back-a{top:148px;height:116px}
.card-front-b{top:276px;height:114px}
.card-back-b{top:403px;height:117px}
.card .wordmark.side{left:10px;top:62px;font-size:10px}
.card .wordmark.centre{left:54px;top:58px;font-size:11px}
.card .photo{left:110px;top:22px;width:30px;height:35px}
.card .person{position:absolute;left:144px;top:22px;font-size:7px;line-height:1.15}
.card .person .person-role{font-size:6px}
.card .person .mobile{font-size:5.5px;color:var(--ink)}
.card .contact{left:110px;top:61px;font-size:5px}
.card .contact svg{width:5px;height:5px}
.card .web{position:absolute;left:0;right:0;top:85px;text-align:center;font-size:5.5px;color:var(--ink)}
.card .web b{color:var(--red);font-weight:400}

/* email signature */
.signature{left:27px;top:478px;width:583px;height:135px}
.signature .wordmark{left:46px;top:80px;font-size:22px}
.signature .photo{left:300px;top:19px;width:42px;height:50px}
.sig-name{position:absolute;left:352px;top:30px;font-size:11px;line-height:1.1}
.sig-name .name{color:var(--red);font-weight:700}
.sig-name .person-role{font-size:9px}
.sig-mobile{position:absolute;left:352px;top:55px;font-size:10px;color:var(--ink)}
.sig-rule{position:absolute;left:300px;top:73px;width:253px;border-top:1px solid var(--rule)}
.signature .contact{left:300px;top:78px;font-size:9.5px;line-height:1.3;color:var(--ink)}
.signature .contact svg{width:8px;height:8px}
.signature .contact b{color:var(--blue);font-weight:400}

/* compliments slip */
.slip{left:62px;top:634px;width:474px;height:222px}
.slip .wordmark{left:60px;top:80px;font-size:17px}
.slip-title{position:absolute;right:28px;top:43px;font-size:14px;font-style:italic;color:var(--muted)}

/* envelope */
.env-back{left:620px;top:537px;width:518px;height:225px}
.env-front{left:649px;top:652px;width:518px;height:222px}
.env-front .wordmark{left:60px;top:80px;font-size:16px}
.env-address{position:absolute;left:40px;top:120px;font-size:8.5px;color:var(--muted)}
.env-window{position:absolute;left:34px;top:136px;width:170px;height:45px;border:1px solid #c9cbce;border-radius:6px;background:linear-gradient(180deg,#f3f3f4,var(--window))}
.env-web{position:absolute;right:30px;bottom:22px;font-size:8px;color:var(--muted)}
.env-web b{color:var(--red);font-weight:400}
</style>
</head>
<body>

<svg width="0" height="0" style="position:absolute" aria-hidden="true">
  <symbol id="i-phone" viewBox="0 0 10 10"><path d="M2 1h2l1 2-1.2 1a5 5 0 0 0 2.2 2.2L7 5l2 1v2c0 .6-.4 1-1 1A8 8 0 0 1 1 2c0-.6.4-1 1-1z"/></symbol>
  <symbol id="i-mail" viewBox="0 0 10 10"><path d="M1 2h8v6H1zM1.6 2.6 5 5.4l3.4-2.8z" fill-rule="evenodd"/></symbol>
  <symbol id="i-web" viewBox="0 0 10 10"><path d="M5 .5a4.5 4.5 0 1 0 0 9 4.5 4.5 0 0 0 0-9zm0 1.4a3.1 3.1 0 1 1 0 6.2 3.1 3.1 0 0 1 0-6.2z"/></symbol>
  <symbol id="i-pin" viewBox="0 0 10 10"><path d="M5 .5a3.3 3.3 0 0 0-3.3 3.3C1.7 6.3 5 9.5 5 9.5s3.3-3.2 3.3-5.7A3.3 3.3 0 0 0 5 .5zm0 2a1.3 1.3 0 1 1 0 2.6 1.3 1.3 0 0 1 0-2.6z"/></symbol>
  <symbol id="i-mobile" viewBox="0 0 10 10"><path d="M3 .5h4v9H3zm.8 1v6.2h2.4V1.5z" fill-rule="evenodd"/></symbol>
</svg>

<!-- Letterhead -->
<section class="piece letterhead">
  <svg class="band" viewBox="0 0 298 422" preserveAspectRatio="none" aria-hidden="true">
    <rect class="fill-orange" x="0" y="290" width="298" height="132"/>
    <ellipse class="fill-paper" cx="150" cy="140" rx="210" ry="272"/>
  </svg>
  <div class="wordmark">brightkeyhomes</div>
  <address class="contact">Shop 4, 52 harbour road,<br>merridale qld 4580<br>
    <svg class="icon"><use href="#i-phone"/></svg>07 5512 4087<br>
    <svg class="icon"><use href="#i-mail"/></svg>marcus@brightkeyhomes.com.au<br>
    <svg class="icon"><use href="#i-web"/></svg>www.brightkeyhomes.com.au</address>
</section>

<!-- Fax header -->
<section class="piece fax">
  <svg class="band" viewBox="0 0 298 422" preserveAspectRatio="none" aria-hidden="true">
    <rect class="fill-orange" x="0" y="290" width="298" height="132"/>
    <ellipse class="fill-paper" cx="150" cy="140" rx="210" ry="272"/>
  </svg>
  <div class="wordmark">brightkeyhomes</div>
  <address class="contact">Shop 4, 52 harbour road,<br>merridale qld 4580<br>
    <svg class="icon"><use href="#i-phone"/></svg>07 5512 4087<br>
    <svg class="icon"><use href="#i-mail"/></svg>marcus@brightkeyhomes.com.au<br>
    <svg class="icon"><use href="#i-web"/></svg>www.brightkeyhomes.com.au</address>
  <div class="fax-title">FAX</div>
  <table class="fax-table">
    <tr><td class="label">To:</td><td></td><td class="label">From:</td><td></td></tr>
    <tr><td class="label">Fax:</td><td></td><td class="label">Pages:</td><td></td></tr>
    <tr><td class="label">Phone:</td><td></td><td class="label">Date:</td><td></td></tr>
    <tr><td class="label">Re:</td><td></td><td class="label">CC:</td><td></td></tr>
  </table>
  <div class="fax-options"><span>Urgent</span><span>For Review</span><span>Please comment</span><span>Please Reply</span><span>Please Recycle</span></div>
</section>

<!-- Folder cover -->
<section class="piece cover">
  <svg class="band" viewBox="0 0 313 440" preserveAspectRatio="none" aria-hidden="true">
    <rect class="fill-purple" x="0" y="0" width="313" height="250"/>
    <rect class="fill-orange" x="0" y="250" width="313" height="190"/>
    <ellipse class="fill-paper" cx="160" cy="265" rx="232" ry="180"/>
  </svg>
  <div class="wordmark">brightkeyhomes</div>
</section>

<!-- Business card front A -->
<section class="piece card card-front-a">
  <div class="wordmark side">brightkeyhomes</div>
  <div class="photo" role="img" aria-label="Portrait photo of the principal"></div>
  <div class="person"><div class="person-name">Marcus Delane</div><div class="person-role">Principal</div><div class="mobile">0412558204</div></div>
  <address class="contact">
    <svg class="icon"><use href="#i-pin"/></svg>shop 4, 52 harbour road,<br>&nbsp;&nbsp;merridale qld 4580<br>
    <svg class="icon"><use href="#i-phone"/></svg>07 5512 4087<br>
    <svg class="icon"><use href="#i-mail"/></svg>marcus@brightkeyhomes.com.au<br>
    <svg class="icon"><use href="#i-web"/></svg>www.brightkeyhomes.com.au</address>
</section>

<!-- Business card back A -->
<section class="piece card card-back-a">
  <svg class="band" viewBox="0 0 205 116" preserveAspectRatio="none" aria-hidden="true">
    <rect class="fill-blue" x="0" y="0" width="205" height="116"/>
    <ellipse class="fill-paper" cx="110" cy="62" rx="122" ry="52"/>
  </svg>
  <div class="wordmark centre">brightkeyhomes</div>
  <div class="web">www.<b>brightkeyhomes</b>.com.au</div>
</section>

<!-- Business card front B -->
<section class="piece card card-front-b">
  <svg class="band" viewBox="0 0 205 114" preserveAspectRatio="none" aria-hidden="true">
    <rect class="fill-orange" x="0" y="0" width="205" height="114"/>
    <ellipse class="fill-paper" cx="105" cy="50" rx="130" ry="62"/>
  </svg>
  <div class="wordmark side" style="top:30px">brightkeyhomes</div>
  <div class="photo" role="img" aria-label="Portrait photo of the principal"></div>
  <div class="person"><div class="person-name">Marcus Delane</div><div class="person-role">Principal</div><div class="mobile">0412558204</div></div>
  <address class="contact">
    <svg class="icon"><use href="#i-pin"/></svg>shop 4, 52 harbour road,<br>&nbsp;&nbsp;merridale qld 4580<br>
    <svg class="icon"><use href="#i-phone"/></svg>07 5512 4087<br>
    <svg class="icon"><use href="#i-mail"/></svg>marcus@brightkeyhomes.com.au<br>
    <svg class="icon"><use href="#i-web"/></svg>www.brightkeyhomes.com.au</address>
</section>

<!-- Business card back B -->
<section class="piece card card-back-b">
  <svg class="band" viewBox="0 0 205 117" preserveAspectRatio="none" aria-hidden="true">
    <rect class="fill-purple" x="0" y="0" width="205" height="60"/>
    <ellipse class="fill-paper" cx="100" cy="88" rx="150" ry="66"/>
  </svg>
  <div class="wordmark centre" style="top:74px">brightkeyhomes</div>
  <div class="web" style="top:99px">www.<b>brightkeyhomes</b>.com.au</div>
</section>

<!-- Email signature -->
<section class="piece signature">
  <div class="wordmark">brightkeyhomes</div>
  <div class="photo" role="img" aria-label="Portrait photo of the principal"></div>
  <div class="sig-name"><div class="name">Marcus Delane</div><div class="person-role">Principal</div></div>
  <div class="sig-mobile"><svg class="icon" width="8" height="8"><use href="#i-mobile"/></svg> 0412558204</div>
  <div class="sig-rule"></div>
  <address class="contact">Shop 4, 52 harbour road,merridale qld 4580<br>
    <svg class="icon"><use href="#i-phone"/></svg>07 5512 4087<br>
    <svg class="icon"><use href="#i-mail"/></svg>marcus@brightkeyhomes.com.au<br>
    <svg class="icon"><use href="#i-web"/></svg>www.<b>brightkeyhomes</b>.com.au</address>
</section>

<!-- Compliments slip -->
<section class="piece slip">
  <svg class="band" viewBox="0 0 474 222" preserveAspectRatio="none" aria-hidden="true">
    <rect class="fill-orange" x="0" y="100" width="474" height="122"/>
    <ellipse class="fill-paper" cx="250" cy="40" rx="330" ry="185"/>
  </svg>
  <div class="wordmark">brightkeyhomes</div>
  <div class="slip-title">With Compliments</div>
</section>

<!-- Envelope back -->
<section class="piece env-back">
  <svg class="band" viewBox="0 0 518 225" preserveAspectRatio="none" aria-hidden="true">
    <polygon class="fill-purple" points="0,0 518,0 490,38 32,38"/>
  </svg>
</section>

<!-- Envelope front -->
<section class="piece env-front">
  <div class="wordmark">brightkeyhomes</div>
  <div class="env-address">Shop 4, 52 harbour road, merridale qld 4580</div>
  <div class="env-window"></div>
  <div class="env-web">www.<b>brightkeyhomes</b>.com.au</div>
</section>

</body>
</html>
```